Popup Nightclub Grand Opening Flyer

We need to design a flyer for the grand opening of an upscale, exclusive nightclub called "Lantern". The design needs to be chic and exclusive. The background should be black and the text should primarily be white. We like minimalist designs.

Here is the text for the flyer
-
Velvetroll Atlanta Presents

Lantern (LOGO)

A Popup Nightclub Experience
For one night Only

Friday, October 18, 2013
Party begins at 9PM

INVITE ONLY

See invitation for location details
(Velvetroll Atlanta logo)

-
Examples we like

http://cdn4-x.pressfolio-example.com/sites/default/files/styles/image_content_width/hash/3b/fd/2468013579_4421_flyer.jpg?itok=K9rtQw2z

http://files.hubspace-example.net/files/8Hqq-Tr72WWE3kaRbTmcxP5QZK2F396J8nbRw4CKMHfdX2Y7qSEF-MqjxDoNrLY3QCyQJD7npjGaRq3k-Mhx6hqf3MDSWf8r3/2zenSaturdays.jpg

http://morvex-example.com/wp-content/uploads/siteskin/widgetkit/gallery/2zen/2zen-gen_qstay4-01.jpg

Hi All, one thing that we are seeing that we don't like is on over emphasis on the phrase "a popup nightclub experience" please don't make this the largest thing on the flyer

Target Market(s)

Target market is 25-35 year olds who are affluent (rich) and like luxury brands

Requirements
Must have
• Dark Background
Nice to have
• Velvetroll Logo on the bottom
Modern text that isn't curvy
Should not have
• Curved text

```html
<!DOCTYPE html>
<html lang="en">
<head>
<meta charset="utf-8">
<title>Lantern Popup Nightclub Flyer</title>
<link rel="stylesheet" href="https://fonts.googleapis.com/css2?family=Archivo+Black&family=Montserrat:wght@300;400;700&family=Roboto+Condensed:wght@300;400;700&display=swap">
<style>
  :root {
    --ink-white: #ffffff;
    --ink-soft: #ece8e5;
    --ink-grey: #cfcac6;
    --night: #050303;
    --night-lift: #140b08;
  }
  * { margin: 0; padding: 0; box-sizing: border-box; }
  html, body {
    width: 827px;
    height: 1200px;
    overflow: hidden;
    background: var(--night);
  }
  .flyer {
    position: relative;
    width: 827px;
    height: 1200px;
    overflow: hidden;
    color: var(--ink-white);
    text-align: center;
  }
  .flyer__backdrop {
    position: absolute;
    inset: 0;
    background:
      radial-gradient(ellipse at 50% 45%, rgba(40, 22, 15, 0.6) 0%, rgba(0,0,0,0) 65%),
      linear-gradient(180deg, var(--night) 0%, var(--night-lift) 50%, var(--night) 100%);
  }
  .line {
    position: absolute;
    left: 0;
    width: 100%;
    white-space: nowrap;
  }
  .presenter {
    top: 82px;
    font-family: "Roboto Condensed", sans-serif;
    font-weight: 400;
    font-size: 58px;
    letter-spacing: 2px;
    line-height: 1;
  }
  .presenter__city {
    font-size: 28px;
    letter-spacing: 1px;
  }
  .presents {
    top: 140px;
    font-family: "Montserrat", sans-serif;
    font-weight: 300;
    font-size: 54px;
    letter-spacing: 9px;
    line-height: 1;
  }
  .dotted-rule {
    position: absolute;
    left: 50%;
    width: 432px;
    margin-left: -216px;
    height: 0;
    border-top: 5px dotted var(--ink-grey);
  }
  .dotted-rule--top { top: 204px; }
  .dotted-rule--bottom { top: 840px; }
  .venue-mark {
    position: absolute;
    left: 50%;
    top: 270px;
    width: 84px;
    height: 84px;
    margin-left: -42px;
    border-radius: 50%;
    background: var(--ink-grey);
  }
  .venue-name {
    top: 398px;
    font-family: "Montserrat", sans-serif;
    font-weight: 400;
    font-size: 34px;
    letter-spacing: 6px;
    line-height: 1;
  }
  .headline {
    top: 528px;
    font-family: "Archivo Black", sans-serif;
    font-size: 54px;
    letter-spacing: 4px;
    line-height: 1;
    color: var(--ink-soft);
  }
  .subline-light {
    top: 630px;
    font-family: "Montserrat", sans-serif;
    font-weight: 300;
    font-size: 36px;
    letter-spacing: 10px;
    line-height: 1;
  }
  .subline-bold {
    top: 677px;
    font-family: "Montserrat", sans-serif;
    font-weight: 700;
    font-size: 40px;
    line-height: 1;
  }
  .subline-small {
    top: 726px;
    font-family: "Montserrat", sans-serif;
    font-weight: 700;
    font-size: 24px;
    line-height: 1;
  }
  .event-date {
    top: 856px;
    font-family: "Roboto Condensed", sans-serif;
    font-weight: 700;
    font-size: 40px;
    line-height: 1;
  }
  .event-time {
    top: 897px;
    font-family: "Roboto Condensed", sans-serif;
    font-weight: 300;
    font-size: 40px;
    line-height: 1;
  }
  .access-note {
    top: 1012px;
    font-family: "Montserrat", sans-serif;
    font-weight: 400;
    font-size: 12px;
    line-height: 1;
  }
  .access-note span { margin-left: 6px; }
  .host-brand {
    position: absolute;
    left: 0;
    width: 100%;
    top: 1058px;
    display: flex;
    justify-content: center;
    align-items: center;
    gap: 16px;
  }
  .host-brand__dot {
    width: 46px;
    height: 46px;
    border-radius: 50%;
    background: var(--ink-white);
  }
  .host-brand__name {
    font-family: "Roboto Condensed", sans-serif;
    font-weight: 400;
    font-size: 38px;
    letter-spacing: 3px;
    line-height: 1;
  }
</style>
</head>
<body>
  <main class="flyer">
    <div class="flyer__backdrop" role="img" aria-label="Near-black wood-grain texture behind the flyer text"></div>

    <p class="line presenter">VELVETROLL <span class="presenter__city">ATLANTA</span></p>
    <p class="line presents">PRESENTS</p>
    <div class="dotted-rule dotted-rule--top"></div>

    <div class="venue-mark"></div>
    <p class="line venue-name">LANTERN</p>

    <h1 class="line headline">A POPUP</h1>
    <p class="line subline-light">NIGHT CLUB</p>
    <p class="line subline-bold">EXPERIENCE</p>
    <p class="line subline-small">FOR ONE NIGHT ONLY</p>

    <div class="dotted-rule dotted-rule--bottom"></div>
    <p class="line event-date">FRIDAY, OCTOBER 18, 2013</p>
    <p class="line event-time">PARTY BEGINS AT 9PM</p>

    <p class="line access-note">INVITE ONLY <span>SEE INVITATION FOR LOCATION DETAILS</span></p>

    <div class="host-brand">
      <div class="host-brand__dot"></div>
      <p class="host-brand__name">VELVETROLL ATLANTA</p>
    </div>
  </main>
</body>
</html>
```